Need a website setup for our new removalist business.
Our business is called Harbour Lane Removals and would like a website setup.
We don’t have a website, logo or design as of yet. Our truck is blue so something possibly that works and can incorporate the blue.

```html
<!DOCTYPE html>
<html lang="en">
<head>
<meta charset="utf-8">
<title>Harbour Lane Removals</title>
<link href="https://fonts.googleapis.com/css2?family=Orbitron:wght@700;900&family=Roboto:wght@400;500;700&display=swap" rel="stylesheet">
<style>
:root{
  --blue:#4565a8;
  --blue-dark:#3a5796;
  --ink:#2b2b2b;
  --text:#444;
  --muted:#a9a9a9;
  --light:#f4f4f4;
  --footer:#2a2a2a;
  --white:#fff;
}
*{margin:0;padding:0;box-sizing:border-box}
html,body{width:1200px;height:3608px;overflow:hidden}
body{position:relative;background:var(--white);font-family:'Roboto',sans-serif;color:var(--text)}
.abs{position:absolute}
.display{font-family:'Orbitron',sans-serif;font-weight:900;letter-spacing:1px}
.btn{position:absolute;display:flex;align-items:center;justify-content:center;background:var(--blue);color:var(--white);font-weight:700;font-size:16px;text-transform:uppercase}
.btn-outline{background:var(--white);color:var(--ink);border:2px solid var(--blue);font-size:14px}
.rule{position:absolute;height:3px;background:var(--blue)}
.photo{position:absolute}

/* top bar & header */
.topline{left:0;top:0;width:1200px;height:5px;background:var(--ink)}
.topbar{left:0;top:0;width:1200px;height:40px;background:var(--ink);clip-path:polygon(616px 0,1200px 0,1200px 40px,652px 40px)}
.topbar-info{right:112px;top:11px;color:var(--white);font-size:14px;display:flex;gap:14px;align-items:center}
.topbar-info svg{margin-right:8px;vertical-align:-2px}
.header{left:0;top:40px;width:1200px;height:103px;background:var(--white)}
.brand-tab{left:98px;top:40px;width:210px;height:133px;background:var(--white);clip-path:polygon(0 0,100% 0,100% 78%,86% 100%,14% 100%,0 78%);z-index:3}
.brand{left:112px;top:50px;z-index:4;display:flex;align-items:center;gap:10px}
.brand-square{width:34px;height:34px;background:var(--blue)}
.brand-name{font-family:'Orbitron',sans-serif;font-weight:900;font-size:17px;line-height:22px;color:var(--blue);text-transform:uppercase}
.nav{left:412px;top:83px;display:flex;font-size:15px;font-weight:500;color:var(--ink);text-transform:uppercase}
.nav a{color:inherit;text-decoration:none;position:absolute;white-space:nowrap}
.nav .active{color:var(--blue);text-decoration:underline}
.caret{display:inline-block;margin-left:6px;border:5px solid transparent;border-top-color:var(--ink);vertical-align:-3px}

/* hero */
.hero-photo{left:0;top:143px;width:1200px;height:690px;background:linear-gradient(100deg,#7d7a73 0%,#5b5e66 35%,#3f4a5c 60%,#2f3a4d 100%)}
.hero-kicker{left:111px;top:311px;color:var(--white);font-size:21px;font-weight:700}
.hero-title{left:110px;top:340px;color:var(--white);font-size:42px}
.hero-text{left:112px;top:418px;color:var(--white);font-size:21px;line-height:30px;width:560px}
.dots{left:1138px;top:398px}
.dot{position:absolute;left:0;width:15px;height:15px;border:2px solid var(--white);border-radius:50%}

/* about */
.h-section{font-size:40px;color:var(--ink)}
.h-section span{color:var(--muted)}
.about-text{left:144px;top:968px;width:363px;font-size:15px;line-height:25.6px;text-align:justify;color:var(--text)}
.about-text p+p{margin-top:12px}

/* services */
.services{left:0;top:1455px;width:1200px;height:483px;background:var(--blue)}
.services-title{left:0;top:1515px;width:1200px;text-align:center;color:var(--white);font-size:40px}
.services-text{left:150px;top:1590px;width:900px;text-align:center;color:var(--white);font-size:15px;line-height:26px;font-weight:500}
.card{position:absolute;top:1708px;width:302px;height:458px;background:var(--white);box-shadow:0 4px 12px rgba(0,0,0,.12);text-align:center}
.card-photo{position:absolute;left:7px;top:7px;width:288px;height:217px}
.card h3{position:absolute;top:246px;width:100%;font-size:17px;font-weight:500;color:var(--ink);text-transform:uppercase}
.card .pip{position:absolute;left:147px;top:274px;width:8px;height:8px;border-radius:50%;background:#b7c3de}
.card p{position:absolute;top:292px;left:14px;right:14px;font-size:16px;line-height:26px;color:var(--text)}
.card .btn{top:382px;left:90px;width:123px;height:42px}
.arrow{position:absolute;top:1807px;width:34px;height:34px;border-radius:50%;display:flex;align-items:center;justify-content:center}

/* safe */
.safe-frame{left:112px;top:2271px;width:260px;height:418px;background:#b1b1b1}
.safe-title{left:683px;top:2296px;font-size:33px;line-height:38px;color:var(--ink)}
.safe-title span{color:var(--muted)}
.safe-text{left:686px;top:2398px;width:402px;font-size:15px;line-height:25.7px;text-align:justify}

/* contact */
.contact{left:0;top:2800px;width:1200px;height:454px;background:var(--light)}
.field{position:absolute;background:var(--white);box-shadow:0 1px 6px rgba(0,0,0,.08);font-size:15px;color:#555;padding:18px 18px}

/* footer */
.footer{left:0;top:3254px;width:1200px;height:303px;background:var(--footer)}
.f-head{color:var(--white);font-size:17px;font-weight:500;text-transform:uppercase}
.f-link{position:absolute;color:var(--white);font-size:14px;display:flex;align-items:center;gap:20px}
.f-link i{width:12px;height:12px;border-radius:50%;background:var(--blue);display:block}
.f-info{position:absolute;left:902px;color:var(--white);font-size:12px;line-height:20px}
.f-info b{font-size:14px;font-weight:700}
.bottom{left:0;top:3557px;width:1200px;height:51px;background:var(--blue)}
.copy{left:0;top:3574px;width:1200px;text-align:center;color:var(--white);font-size:12.5px}
.social{position:absolute;top:3563px;width:32px;height:32px;border:2px solid var(--white)}
</style>
</head>
<body>

<!-- header -->
<div class="abs header"></div>
<div class="abs topline"></div>
<div class="abs topbar"></div>
<div class="abs topbar-info">
  <span><svg width="13" height="13" viewBox="0 0 24 24"><path fill="#6f8fd4" d="M6.6 10.8a15 15 0 006.6 6.6l2.2-2.2c.3-.3.7-.4 1-.2 1.1.4 2.3.6 3.6.6.6 0 1 .4 1 1V20c0 .6-.4 1-1 1A17 17 0 013 4c0-.6.4-1 1-1h3.5c.6 0 1 .4 1 1 0 1.3.2 2.5.6 3.6.1.3 0 .7-.2 1z"/></svg>+1 (555) 210 4477</span>
  <span>|</span>
  <span><svg width="14" height="11" viewBox="0 0 24 18"><path fill="#6f8fd4" d="M0 0h24v18H0zM2 2l10 7 10-7"/><path fill="none" stroke="#2b2b2b" stroke-width="2" d="M1 1l11 8 11-8"/></svg>info@harbourlaneremovals.com</span>
</div>
<div class="abs brand-tab"></div>
<div class="abs brand">
  <div class="brand-square"></div>
  <div class="brand-name">Harbour Lane<br>Removals</div>
</div>
<nav class="abs nav">
  <a class="active" style="left:0">Home</a>
  <a style="left:74px">About Us</a>
  <a style="left:179px">Our Services<span class="caret"></span></a>
  <a style="left:331px">Blog</a>
  <a style="left:401px">Contact Us</a>
</nav>
<div class="btn" style="left:942px;top:67px;width:146px;height:51px">Get a Quote</div>

<!-- hero -->
<div class="photo hero-photo" role="img" aria-label="Smiling removalist in cap and work jacket, arms crossed, in front of a blue moving van"></div>
<div class="abs hero-kicker">HARBOUR LANE REMOVALS</div>
<div class="abs display hero-title">MOVING MADE EASY</div>
<div class="rule" style="left:112px;top:394px;width:54px;background:var(--white)"></div>
<div class="abs hero-text">Lorem ipsum dolor sit amet, consectetur adipiscing elit, sed do eiusmod incididunt ut laborea.</div>
<div class="btn" style="left:112px;top:501px;width:154px;height:51px">Get Started</div>
<div class="abs dots">
  <div class="dot" style="top:0"></div>
  <div class="dot" style="top:24px;background:var(--white)"></div>
  <div class="dot" style="top:49px"></div>
  <div class="dot" style="top:74px"></div>
</div>
<svg class="abs" style="left:0;top:640px" width="1200" height="200" viewBox="0 0 1200 200">
  <polygon points="0,172 301,18 1200,123 1200,200 0,200" fill="#4565a8"/>
  <polygon points="0,172 301,28 1200,187 1200,200 0,200" fill="#fff"/>
  <polygon points="0,172 301,18 305,26 0,178" fill="#fff"/>
</svg>

<!-- about -->
<div class="abs display h-section" style="left:143px;top:888px">ABOUT <span>US</span></div>
<div class="rule" style="left:112px;top:940px;width:42px"></div>
<div class="abs about-text">
  <p>Lorem ipsum dolor sit amet, consectetur adipiscing elit, sed do eiusmod tempor incididunt ut labore et dolore magna aliqua. Ut enim ad minim veniam, quis nostrud exercitation ullamco laboris nisi ut aliquip ex ea commodo consequat. Duis aute irure dolor in reprehenderit in voluptate velit esse cillum dolore eu fugiat nulla pariatur.</p>
  <p>Lorem ipsum dolor sit amet, consectetur adipiscing elit, sed do eiusmod tempor incididunt ut labore et dolore magna aliquea.</p>
</div>
<div class="btn" style="left:144px;top:1264px;width:147px;height:52px">Learn More</div>
<div class="photo" style="left:626px;top:862px;width:462px;height:427px;background:linear-gradient(135deg,#b58d5f,#8a6a48 45%,#2f4f99 75%,#c79a66)" role="img" aria-label="Two movers in blue uniforms carrying a rolled rug and a cardboard box"></div>
<div class="photo" style="left:563px;top:1106px;width:279px;height:245px;background:linear-gradient(135deg,#e8e5df,#d2c6b5 50%,#b48a5e);border-top:3px solid #fff;border-right:3px solid #fff" role="img" aria-label="Happy couple embracing among moving boxes in a new living room"></div>

<!-- services -->
<div class="abs services" role="img" aria-label="Blue tinted background of a bright room"></div>
<div class="abs display services-title">OUR SERVICES</div>
<div class="rule" style="left:580px;top:1562px;width:40px;background:var(--white)"></div>
<div class="abs services-text">Lorem ipsum dolor sit amet, consectetur adipiscing elit, sed do eiusmod tempor incididunt ut labore et dolore magna aliqua. Ut enim ad minim veniam, quis nostrud exercitation ullamco laboris nisi ut aliquip ex ea commodo consequat. Duis aute irure dolor in reprehenderit in voluptate velit esse cillum dolore eu fugiat nulla pariaturea.</div>

<div class="arrow" style="left:33px;background:#6580bb"><svg width="12" height="12" viewBox="0 0 12 12"><path d="M8 1L3 6l5 5" fill="none" stroke="#fff" stroke-width="2"/></svg></div>
<div class="arrow" style="left:1131px;background:#fff"><svg width="12" height="12" viewBox="0 0 12 12"><path d="M4 1l5 5-5 5" fill="none" stroke="#333" stroke-width="2"/></svg></div>

<div class="card" style="left:112px">
  <div class="card-photo" style="background:linear-gradient(160deg,#a9c0dc,#b98d5c 55%,#2e4f97)" role="img" aria-label="Movers unloading boxes from a truck"></div>
  <h3>Residential Moving</h3><span class="pip"></span>
  <p>Lorem ipsum dolor sit amet, consec adipiscing elit, sed do eiusmod tempor incididuntea.</p>
  <div class="btn btn-outline">Learn More</div>
</div>
<div class="card" style="left:448px">
  <div class="card-photo" style="background:linear-gradient(160deg,#e6e3de,#c9a57a 55%,#d8d4cc)" role="img" aria-label="Office space stacked with packed boxes"></div>
  <h3>Commercial Moving</h3><span class="pip"></span>
  <p>Lorem ipsum dolor sit amet, consec adipiscing elit, sed do eiusmod tempor incididuntea.</p>
  <div class="btn" style="font-size:14px">Learn More</div>
</div>
<div class="card" style="left:785px">
  <div class="card-photo" style="background:linear-gradient(160deg,#8fa47a,#c7a679 50%,#a9a49a)" role="img" aria-label="Movers carrying wrapped furniture outside a house"></div>
  <h3>Packing Services</h3><span class="pip"></span>
  <p>Lorem ipsum dolor sit amet, consec adipiscing elit, sed do eiusmod tempor incididuntea.</p>
  <div class="btn btn-outline">Learn More</div>
</div>

<!-- safe, trusted -->
<div class="abs safe-frame"></div>
<div class="photo" style="left:151px;top:2310px;width:454px;height:340px;background:linear-gradient(135deg,#ecebe8,#c9b49a 45%,#7a6a5e 80%,#e5e1da)" role="img" aria-label="Family sitting under a cardboard roof in front of a sofa"></div>
<div class="abs display safe-title">SAFE, TRUSTED<br><span>MOVING</span></div>
<div class="rule" style="left:659px;top:2372px;width:45px"></div>
<div class="abs safe-text">Sed ut perspiciatis unde omnis iste natus error sit voluptatem accusantium doloremque laudantium, totam rem aperiam, eaque ipsa quae ab illo inventore veritatis et quasi architecto beatae vitae dicta sunt explicabo. Nemo enim ipsam voluptatem quia voluptas sit aspernatur aut odit aut fugit, sed quia consequuntur magni dolores eos qui ratione voluptatem sequi nesciunt.</div>
<div class="btn" style="left:686px;top:2610px;width:147px;height:50px">Contact Us</div>

<!-- get in touch -->
<div class="abs contact"></div>
<div class="abs display h-section" style="left:0;top:2868px;width:1200px;text-align:center">GET <span>IN TOUCH</span></div>
<div class="rule" style="left:572px;top:2917px;width:56px"></div>
<div class="field" style="left:165px;top:2957px;width:283px;height:48px">Full Name</div>
<div class="field" style="left:458px;top:2957px;width:283px;height:48px">Phone</div>
<div class="field" style="left:752px;top:2957px;width:283px;height:48px">Email Address</div>
<div class="field" style="left:165px;top:3020px;width:870px;height:91px">Message</div>
<div class="btn" style="left:518px;top:3128px;width:163px;height:49px">Send Message</div>

<!-- footer -->
<div class="abs footer"></div>
<div class="abs brand" style="top:3390px">
  <div class="brand-square"></div>
  <div class="brand-name" style="color:var(--white)">Harbour Lane<br>Removals</div>
</div>
<div class="abs f-head" style="left:421px;top:3312px">Quick Links</div>
<div class="f-link" style="left:423px;top:3352px"><i></i>Home</div>
<div class="f-link" style="left:423px;top:3388px"><i></i>About Us</div>
<div class="f-link" style="left:423px;top:3424px"><i></i>Our Services</div>
<div class="f-link" style="left:423px;top:3460px"><i></i>Blog</div>
<div class="f-link" style="left:423px;top:3496px"><i></i>Contact Us</div>
<div class="f-link" style="left:631px;top:3352px"><i></i>Site Map</div>
<div class="f-link" style="left:631px;top:3388px"><i></i>Disclaimer</div>
<div class="f-link" style="left:631px;top:3424px"><i></i>Privacy Policy</div>
<div class="f-link" style="left:631px;top:3460px"><i></i>Terms Of Use</div>
<div class="abs f-head" style="left:865px;top:3312px">Contact Info</div>
<svg class="abs" style="left:866px;top:3352px" width="10" height="14" viewBox="0 0 10 14"><path d="M5 0a5 5 0 00-5 5c0 4 5 9 5 9s5-5 5-9a5 5 0 00-5-5zm0 7a2 2 0 110-4 2 2 0 010 4z" fill="#4565a8"/></svg>
<div class="f-info" style="top:3350px"><b>ADDRESS:</b><br>12 Quayside Road, Dockside,<br>Australia</div>
<svg class="abs" style="left:865px;top:3432px" width="13" height="13" viewBox="0 0 24 24"><path fill="#4565a8" d="M6.6 10.8a15 15 0 006.6 6.6l2.2-2.2c.3-.3.7-.4 1-.2 1.1.4 2.3.6 3.6.6.6 0 1 .4 1 1V20c0 .6-.4 1-1 1A17 17 0 013 4c0-.6.4-1 1-1h3.5c.6 0 1 .4 1 1 0 1.3.2 2.5.6 3.6.1.3 0 .7-.2 1z"/></svg>
<div class="f-info" style="top:3430px"><b>PHONE:</b><br>+1 (555) 210 4477</div>
<svg class="abs" style="left:865px;top:3486px" width="14" height="10" viewBox="0 0 24 18"><path fill="#4565a8" d="M0 0h24v18H0z"/><path fill="none" stroke="#2a2a2a" stroke-width="2" d="M1 1l11 8 11-8"/></svg>
<div class="f-info" style="top:3483px"><b>EMAIL:</b><br>info@harbourlaneremovals.com</div>
<div class="abs bottom"></div>
<div class="abs copy">© 2024 HARBOUR LANE REMOVALS &nbsp;|&nbsp; All Rights Reserved</div>
<div class="social" style="left:976px;background:var(--white)" aria-label="Social link"></div>
<div class="social" style="left:1016px" aria-label="Social link"></div>
<div class="social" style="left:1056px" aria-label="Social link"></div>

</body>
</html>
```